Kelvor Guard Installations - Alarm and CCTV installation Flyer

Need a flyer designed that grabs the attention of potential customers, we need the price to stand out the most to grab people’s attention, whether they are residential or commercial.We are a security company based in Brentwood Essex but cover London and the home counties. here is our website to take a look at www.kelvorguardinstalls.co.uk. We want them to know we install complete alarm and Cctv systems and will keep them “safe”

Target Market(s)

residential and commercial property

Colors
f37122

Requirements
Must have
• on one side
• large clear logo - professional design
• - Intruder Alarms starting from £495 + VAT. (Big text)
• - £150 discount on installations
• *terms and conditions apply (small text)
• - Not happy with your current provider? Free of charge no obligation take over survey and quotation and up to £100 off
• - CCTV systems starting from £595 + VAT (based on 2 cameras)
• Kelvor Guard Installations are always there, always available, wherever and whenever you need us.
• Large telephone number at the bottom 01632 908417
• Address / email / website as a footer * see website for details
• on second side
• large and bold
• Are you looking to keep you and your premises safe?
• - Kelvor Guard Installations install, maintain and repair all intruder alarms, CCTV, intercom and access control
• - View, control and manage your security systems anywhere in the world
• - Feel at ease with monitoring services & police response tailored to suit you and your business
• - Kelvor Guard can takeover any existing security system and offer maintenance checks to guarantee the best performance for you and your premises
• - Kelvor Guard understand that being security conscious is ever increasing, protecting your property and family is a number one priority
• - Our fully insured and accredited team offer quality, safety and cost efficiency throughout the whole process
• - Kelvor Guard Installations are using the latest cloud-based technology to stay connected with your home and business 24/7
• If you are looking to improve the security in your home, office or commercial property then call a member of our team today for a free quote.
• Fully insured and accredited
• Tradevouch logo and NQPRB Intruder and CCTV logos
• Logo somewhere on page and
• Telephone number
• Address / email / website as footer
Nice to have
• We would like to have the text saying
• Intruder alarms installed from £495 + vat the biggest text on the page. Most likely the £495 part the largest.
• Also would like “not happy with your current provider” more obvious
• We would like use our company colours - Orange/White/black

```html
<!DOCTYPE html>
<html lang="en">
<head>
<meta charset="utf-8">
<title>Kelvor Guard Installations – Alarm and CCTV Flyer</title>
<link href="https://fonts.googleapis.com/css2?family=Lato:ital,wght@0,400;0,700;0,900;1,400;1,700&family=Oswald:wght@500;600&display=swap" rel="stylesheet">
<style>
  :root {
    --red: #e42b24;
    --red-dark: #b81d18;
    --ink: #2a2a2a;
    --ink-deep: #222222;
    --white: #ffffff;
    --band: #e8e8e8;
    --stage: #a7a7a7;
  }
  * { margin: 0; padding: 0; box-sizing: border-box; }
  html, body { width: 1200px; height: 902px; overflow: hidden; }
  body { background: var(--stage); font-family: "Lato", sans-serif; position: relative; }

  .flyer { position: absolute; width: 478px; height: 671px; overflow: hidden; background: var(--white); }
  .flyer--front { left: 102px; top: 94px; }
  .flyer--back { left: 637px; top: 138px; width: 480px; }
  .flyer__bg { position: absolute; inset: 0; width: 100%; height: 100%; }
  .abs { position: absolute; }
  .cond { font-family: "Oswald", sans-serif; font-weight: 600; text-transform: uppercase; white-space: nowrap; }

  /* brand name */
  .brand { color: var(--red); font-family: "Lato", sans-serif; font-weight: 700; text-align: center; text-transform: uppercase; line-height: 1; white-space: nowrap; }
  .brand__name { font-size: 25px; letter-spacing: 0.5px; }
  .brand__sub { font-size: 14px; letter-spacing: 3px; margin-top: 7px; }
  .front-brand { left: 14px; top: 62px; width: 220px; }

  /* front hero */
  .hero { left: 34px; top: 180px; color: var(--white); }
  .hero__title { font-size: 37px; line-height: 37px; font-weight: 900; }
  .hero__from { font-size: 22px; margin-top: 10px; font-weight: 900; }
  .hero__price { font-size: 50px; line-height: 56px; color: var(--ink-deep); }

  .discount { left: 50px; top: 364px; width: 156px; text-align: center; color: var(--ink-deep); }
  .discount__amount { font-size: 40px; line-height: 44px; color: var(--red); }
  .discount__label { font-size: 19px; line-height: 21px; }
  .discount__note { font-size: 10px; line-height: 12px; color: var(--red); }
  .discount__terms { font-size: 7.5px; font-family: "Lato", sans-serif; font-style: italic; font-weight: 400; text-transform: none; margin-top: 3px; line-height: 1.15; }

  .switch { left: 240px; top: 344px; width: 226px; color: var(--white); font-size: 23px; line-height: 29px; text-align: center; }
  .switch-offer { left: 253px; top: 414px; width: 198px; height: 44px; background: var(--white); border-radius: 5px; display: flex; align-items: center; padding: 0 6px; }
  .switch-offer__text { width: 88px; text-align: center; color: var(--ink-deep); font-size: 5.6px; line-height: 7px; font-weight: 500; white-space: normal; }
  .switch-offer__free { color: var(--red); font-size: 12px; line-height: 13px; font-weight: 600; }
  .switch-offer__amount { font-size: 36px; color: var(--ink-deep); margin-left: 4px; line-height: 1; }
  .switch-offer__off { color: var(--red); font-size: 14px; writing-mode: vertical-rl; transform: rotate(180deg); margin-left: 3px; line-height: 1; }

  .cctv { left: 29px; top: 505px; color: var(--white); }
  .cctv__line { font-size: 15.5px; font-weight: 700; text-transform: uppercase; }
  .cctv__note { font-size: 11px; margin-left: 26px; margin-top: 2px; font-weight: 500; }
  .cctv-price { left: 286px; top: 492px; width: 92px; text-align: center; color: var(--ink-deep); font-size: 34px; line-height: 46px; }
  .cctv-vat { left: 390px; top: 498px; color: var(--white); font-size: 20px; font-weight: 700; }

  .call { left: 34px; top: 566px; display: flex; align-items: center; }
  .call__label { font-weight: 900; font-size: 21px; color: var(--ink-deep); }
  .call__icon { width: 30px; height: 30px; margin: 0 22px 0 14px; }
  .call__number { font-size: 40px; color: var(--red); line-height: 1; letter-spacing: 0.5px; }

  .contact { display: flex; align-items: center; gap: 6px; color: var(--white); font-size: 7px; line-height: 8.5px; white-space: nowrap; }
  .contact svg { width: 15px; height: 15px; flex: none; }
  .front-contact { top: 633px; }

  /* back */
  .back-head { left: 30px; top: 24px; white-space: nowrap; }
  .back-head__ask { font-size: 31px; line-height: 38px; color: var(--ink-deep); }
  .back-head__keep { font-size: 21px; line-height: 26px; color: var(--white); }
  .back-head__safe { left: 298px; top: 12px; font-size: 70px; line-height: 86px; color: var(--white); }

  .services { left: 26px; top: 358px; width: 296px; list-style: none; color: var(--white); font-size: 7.3px; line-height: 9px; }
  .services li { display: flex; gap: 9px; margin-bottom: 6.6px; }
  .services svg { width: 10px; height: 10px; flex: none; margin-top: 1px; }
  .services em { font-weight: 700; }

  .back-brand { left: 8px; top: 600px; width: 184px; }
  .back-brand .brand__name { font-size: 22px; }
  .back-brand .brand__sub { font-size: 13px; margin-top: 8px; }
  .partner-name { left: 318px; top: 546px; font-size: 17px; font-weight: 700; color: var(--red); letter-spacing: -0.3px; }
  .back-pitch { left: 198px; top: 580px; width: 276px; font-size: 7.4px; line-height: 9px; font-style: italic; color: var(--ink-deep); }
</style>
</head>
<body>

<section class="flyer flyer--front" aria-label="Flyer front">
  <svg class="flyer__bg" viewBox="0 0 478 671" aria-hidden="true">
    <defs>
      <linearGradient id="photoTone" x1="0" y1="0" x2="0" y2="1">
        <stop offset="0" stop-color="#f4f4f4"/>
        <stop offset="1" stop-color="#cfcfcf"/>
      </linearGradient>
      <radialGradient id="badgeRed" cx="0.4" cy="0.35" r="0.7">
        <stop offset="0" stop-color="#ff5a4f"/>
        <stop offset="1" stop-color="#c41b15"/>
      </radialGradient>
    </defs>
    <rect width="478" height="671" fill="#ffffff"/>
    <polygon points="0,130 478,80 478,270 0,381" fill="#e42b24"/>
    <polygon points="0,381 478,270 478,548 0,548" fill="#2a2a2a"/>
    <rect y="548" width="478" height="74" fill="#e8e8e8"/>
    <rect y="622" width="478" height="49" fill="#2a2a2a"/>
    <polygon points="128,354 206,386 206,438 128,470 50,438 50,386" fill="#ffffff"/>
    <polygon points="128,361 199,390 199,434 128,463 57,434 57,390" fill="none" stroke="#9a9a9a" stroke-width="1.2" stroke-dasharray="2 2"/>
    <circle cx="332" cy="515" r="48" fill="#d9d9d9"/>
    <circle cx="332" cy="515" r="43" fill="url(#badgeRed)"/>
  </svg>
  <svg class="abs" style="left:0;top:0" width="478" height="671" role="img" aria-label="Photo of a hand pressing an alarm keypad showing Welcome Home">
    <polygon points="258,28 452,28 478,60 478,262 258,313" fill="url(#photoTone)"/>
  </svg>

  <div class="abs brand front-brand">
    <div class="brand__name">Kelvor Guard</div>
    <div class="brand__sub">Installations</div>
  </div>

  <div class="abs hero">
    <div class="hero__title">INTRUDER<br>ALARMS</div>
    <div class="hero__from">STARTING FROM</div>
    <div class="hero__price cond">£495 + VAT</div>
  </div>

  <div class="abs discount cond">
    <div class="discount__amount">£150</div>
    <div class="discount__label">Discount</div>
    <div class="discount__note">On installations</div>
    <div class="discount__terms">*terms and conditions<br>apply</div>
  </div>

  <div class="abs switch cond">Not happy with your<br>current provider?</div>
  <div class="abs switch-offer cond">
    <div class="switch-offer__text">
      <div class="switch-offer__free">Free of charge</div>
      No obligation take over survey and quotation and up to
    </div>
    <div class="switch-offer__amount">£100</div>
    <div class="switch-offer__off">Off</div>
  </div>

  <div class="abs cctv">
    <div class="cctv__line">CCTV systems starting from</div>
    <div class="cctv__note cond">(Based on 2 cameras)</div>
  </div>
  <div class="abs cctv-price cond">£595</div>
  <div class="abs cctv-vat">+ VAT</div>

  <div class="abs call">
    <span class="call__label">CALL US !</span>
    <svg class="call__icon" viewBox="0 0 30 30" aria-hidden="true">
      <circle cx="15" cy="15" r="13.5" fill="none" stroke="#222" stroke-width="2"/>
      <path d="M10.5 8.5l2.5-.5 1.5 3.5-1.8 1.3c.8 1.8 2.2 3.2 4 4l1.3-1.8 3.5 1.5-.5 2.5c-.3 1-1.3 1.6-2.3 1.4-4.5-.9-8-4.4-8.9-8.9-.2-1 .4-2 1.4-2.3z" fill="#222"/>
    </svg>
    <span class="call__number cond">01632 908417</span>
  </div>

  <div class="abs contact front-contact" style="left:30px">
    <svg viewBox="0 0 16 16" aria-hidden="true"><circle cx="8" cy="8" r="8" fill="#e42b24"/><path d="M8 3.5l4.5 4h-1.3v4.5H4.8V7.5H3.5z" fill="#fff"/></svg>
    <span>14 Harwell Lane,<br>Brentwood, Essex, CM14 9ZX</span>
  </div>
  <div class="abs contact front-contact" style="left:175px;top:637px">
    <svg viewBox="0 0 16 16" aria-hidden="true"><circle cx="8" cy="8" r="8" fill="#e42b24"/><rect x="4" y="5" width="8" height="6" fill="#fff"/><path d="M4 5l4 3.2L12 5" fill="none" stroke="#e42b24" stroke-width="0.9"/></svg>
    <span>operations@kelvorguardinstalls.co.uk</span>
  </div>
  <div class="abs contact front-contact" style="left:330px;top:637px">
    <svg viewBox="0 0 16 16" aria-hidden="true"><circle cx="8" cy="8" r="8" fill="#e42b24"/><circle cx="8" cy="8" r="4.2" fill="none" stroke="#fff" stroke-width="1"/><path d="M3.8 8h8.4M8 3.8v8.4" stroke="#fff" stroke-width="0.8"/></svg>
    <span>www.kelvorguardinstalls.co.uk</span>
  </div>
</section>

<section class="flyer flyer--back" aria-label="Flyer back">
  <svg class="flyer__bg" viewBox="0 0 480 671" aria-hidden="true">
    <defs>
      <linearGradient id="headRed" x1="0" y1="0" x2="0" y2="1">
        <stop offset="0" stop-color="#ee3a31"/>
        <stop offset="1" stop-color="#c81f1a"/>
      </linearGradient>
    </defs>
    <rect width="480" height="671" fill="#ffffff"/>
    <rect width="480" height="100" fill="url(#headRed)"/>
    <rect y="349" width="480" height="185" fill="#2a2a2a"/>
    <rect x="192" y="616" width="288" height="44" fill="#e42b24"/>
    <circle cx="231" cy="560" r="18" fill="#ffffff" stroke="#8a8a8a" stroke-width="1.2"/>
    <rect x="256" y="543" width="28" height="34" fill="#ffffff" stroke="#8a8a8a" stroke-width="1.2"/>
    <circle cx="301" cy="556" r="13" fill="#ffffff" stroke="#8a8a8a" stroke-width="1.2"/>
  </svg>
  <svg class="abs" style="left:0;top:100px" width="480" height="249" role="img" aria-label="Photo of a wall-mounted alarm keypad in a modern home interior">
    <defs>
      <linearGradient id="roomTone" x1="0" y1="0" x2="1" y2="1">
        <stop offset="0" stop-color="#cfd3d6"/>
        <stop offset="1" stop-color="#eceeef"/>
      </linearGradient>
    </defs>
    <rect width="480" height="249" fill="url(#roomTone)"/>
  </svg>
  <svg class="abs" style="left:323px;top:366px" width="132" height="160" role="img" aria-label="Two smartphones showing the security control app">
    <rect width="132" height="160" rx="8" fill="#3b4a5a"/>
  </svg>

  <div class="abs back-head cond">
    <div class="back-head__ask">Are you looking to</div>
    <div class="back-head__keep">Keep you and your premises</div>
  </div>
  <div class="abs back-head__safe cond">Safe?</div>

  <ul class="abs services">
    <li><svg viewBox="0 0 10 10" aria-hidden="true"><rect width="10" height="10" fill="#e42b24"/><path d="M2.2 5.2l2 2 3.8-4" fill="none" stroke="#fff" stroke-width="1.3"/></svg><span>Kelvor Guard Installations <em>install, maintain and repair</em> all intruder alarms, CCTV, intercom and access control</span></li>
    <li><svg viewBox="0 0 10 10" aria-hidden="true"><rect width="10" height="10" fill="#e42b24"/><path d="M2.2 5.2l2 2 3.8-4" fill="none" stroke="#fff" stroke-width="1.3"/></svg><span>View, control and manage your security systems <em>anywhere in the world</em></span></li>
    <li><svg viewBox="0 0 10 10" aria-hidden="true"><rect width="10" height="10" fill="#e42b24"/><path d="M2.2 5.2l2 2 3.8-4" fill="none" stroke="#fff" stroke-width="1.3"/></svg><span>Feel at ease with monitoring services &amp; police response tailored to suit you and your business</span></li>
    <li><svg viewBox="0 0 10 10" aria-hidden="true"><rect width="10" height="10" fill="#e42b24"/><path d="M2.2 5.2l2 2 3.8-4" fill="none" stroke="#fff" stroke-width="1.3"/></svg><span>Kelvor Guard can takeover any existing security system and offer maintenance checks to guarantee the best performance for you and your premises</span></li>
    <li><svg viewBox="0 0 10 10" aria-hidden="true"><rect width="10" height="10" fill="#e42b24"/><path d="M2.2 5.2l2 2 3.8-4" fill="none" stroke="#fff" stroke-width="1.3"/></svg><span>Kelvor Guard understand that being security conscious is ever increasing, protecting your property and family is a number one priority</span></li>
    <li><svg viewBox="0 0 10 10" aria-hidden="true"><rect width="10" height="10" fill="#e42b24"/><path d="M2.2 5.2l2 2 3.8-4" fill="none" stroke="#fff" stroke-width="1.3"/></svg><span>Our fully insured and accredited team <em>offer quality, safety and cost efficiency</em> throughout the whole process</span></li>
    <li><svg viewBox="0 0 10 10" aria-hidden="true"><rect width="10" height="10" fill="#e42b24"/><path d="M2.2 5.2l2 2 3.8-4" fill="none" stroke="#fff" stroke-width="1.3"/></svg><span>Kelvor Guard Installations are using the latest <em>cloud-based technology</em> to stay connected with your home and business <span style="color:var(--red)">24/7</span></span></li>
  </ul>

  <div class="abs brand back-brand">
    <div class="brand__name">Kelvor Guard</div>
    <div class="brand__sub">Installations</div>
  </div>

  <div class="abs partner-name">Tradevouch</div>

  <p class="abs back-pitch">If you are looking to improve the security in your home, office or commercial property then call a member of our team today for a free quote.</p>

  <div class="abs contact" style="left:202px;top:621px">
    <svg viewBox="0 0 16 16" aria-hidden="true" style="width:11px;height:11px"><circle cx="8" cy="8" r="8" fill="#fff"/><path d="M8 3.5l4.5 4h-1.3v4.5H4.8V7.5H3.5z" fill="#e42b24"/></svg>
    <span>14 Harwell Lane,<br>Brentwood, Essex, CM14 9ZX</span>
  </div>
  <div class="abs contact" style="left:202px;top:644px">
    <svg viewBox="0 0 16 16" aria-hidden="true" style="width:11px;height:11px"><circle cx="8" cy="8" r="8" fill="#fff"/><path d="M5.5 4.5l1.8-.3 1 2.3-1.2.9c.5 1.2 1.5 2.1 2.6 2.6l.9-1.2 2.3 1-.3 1.8c-.2.6-.8 1-1.5.9-2.9-.6-5.2-2.9-5.8-5.8-.1-.7.3-1.3.9-1.5z" fill="#e42b24"/></svg>
    <span>01632 908417</span>
  </div>
  <div class="abs contact" style="left:342px;top:622px">
    <svg viewBox="0 0 16 16" aria-hidden="true" style="width:11px;height:11px"><circle cx="8" cy="8" r="8" fill="#fff"/><rect x="4" y="5" width="8" height="6" fill="#e42b24"/></svg>
    <span>operations@kelvorguardinstalls.co.uk</span>
  </div>
  <div class="abs contact" style="left:342px;top:637px">
    <svg viewBox="0 0 16 16" aria-hidden="true" style="width:11px;height:11px"><circle cx="8" cy="8" r="8" fill="#fff"/><circle cx="8" cy="8" r="4" fill="none" stroke="#e42b24" stroke-width="1.2"/></svg>
    <span>www.kelvorguardinstalls.co.uk</span>
  </div>
</section>

</body>
</html>
```